Automotive spring company needs banner for website

Banner dimensions: 3840 x 880 pixels
Banner need to be consistent with our branding (logo, stationary, colors, fonts, message).
People images should show happiness and it is preferable those people are in or around a car unless it ties into one of the 3 quotes in the must haves below.
Use color blue #4885ed
and gold color #f7d105
Minimal, strong, clean, & tech

35-55 male and female

Auto Repair

• Clickable element for "Shop" or "Make an Appointment"
• "25 Years of Customer Satisfaction" or
• "Get it Done Right by Specialist" or
• "Peace of Mind National Warranty"
• Use our font, Eurostile and/or complimentary font paring

```html
<!DOCTYPE html>
<html lang="en">
<head>
<meta charset="UTF-8">
<title>Coilwell – 25 Years of Customer Satisfaction</title>
<link href="https://fonts.googleapis.com/css2?family=Michroma&display=swap" rel="stylesheet">
<style>
  :root {
    --brand-gold: #f7d105;
    --brand-blue: #4885ed;
    --text-light: #ffffff;
    --wall-light: #1f2c31;
    --wall-mid: #111a1f;
    --wall-dark: #05090d;
    --portrait-light: #8a7566;
    --portrait-dark: #3a302b;
  }
  * { margin: 0; padding: 0; box-sizing: border-box; }
  html, body {
    width: 1200px;
    height: 275px;
    overflow: hidden;
    background: var(--wall-dark);
  }
  .banner {
    position: relative;
    width: 1200px;
    height: 275px;
    overflow: hidden;
    font-family: "Michroma", sans-serif;
    color: var(--text-light);
    background:
      radial-gradient(ellipse 420px 260px at 180px 90px, var(--wall-light) 0%, transparent 70%),
      linear-gradient(90deg, var(--wall-mid) 0%, #0c1418 45%, var(--wall-dark) 100%);
  }
  .portrait {
    position: absolute;
    left: 196px;
    top: 12px;
    width: 196px;
    height: 260px;
    border-radius: 90px 90px 0 0;
    background: linear-gradient(180deg, var(--portrait-dark) 0%, var(--portrait-light) 45%, #d9d4cc 75%, #e8e4dc 100%);
    opacity: 0.85;
  }
  .headline {
    position: absolute;
    left: 488px;
    top: 88px;
    text-transform: uppercase;
  }
  .headline__number {
    display: block;
    font-size: 46px;
    line-height: 1;
    color: var(--brand-gold);
    letter-spacing: 1px;
  }
  .headline__text {
    display: block;
    margin-top: 8px;
    font-size: 19.5px;
    line-height: 25px;
    letter-spacing: 0.5px;
  }
  .brand-name {
    position: absolute;
    right: 36px;
    top: 33px;
    font-size: 21px;
    color: var(--brand-gold);
    letter-spacing: 1px;
  }
  .cta {
    position: absolute;
    right: 24px;
    top: 238px;
    font-size: 13px;
    color: var(--text-light);
    text-decoration: none;
    letter-spacing: 0.3px;
  }
  .accent-line {
    position: absolute;
    left: 0;
    bottom: 0;
    width: 100%;
    height: 2px;
    background: var(--brand-blue);
  }
</style>
</head>
<body>
  <section class="banner">
    <div class="portrait" role="img" aria-label="Photo of a smiling woman with shoulder-length wavy brown hair in a white lace top, standing against a dark wall"></div>

    <h1 class="headline">
      <span class="headline__number">25</span>
      <span class="headline__text">Years of<br>Customer Satisfaction</span>
    </h1>

    <div class="brand-name">COILWELL</div>

    <a class="cta" href="#appointment">BOOK APPOINTMENT &gt;</a>

    <div class="accent-line"></div>
  </section>
</body>
</html>
```